Redesign of business card for Cedar Ridge Mechanical

We are looking for a new design for our business cards for Cedar Ridge Mechanical. We are a plumbing & HVAC construction company, operating on the West Coast of Canada and USA. Logo attached.
Industry/Entity Type
Construction - Plumbing & HVAC
Contact Information for Business Card
Name, address, phone numbers, email, website address
Look and feel
Each slider illustrates characteristics of the customer's brand and the style your logo design should communicate.

```html
<!DOCTYPE html>
<html lang="en">
<head>
<meta charset="utf-8">
<title>Cedar Ridge Mechanical – Business Card</title>
<link href="https://fonts.googleapis.com/css2?family=Open+Sans:wght@400;700&display=swap" rel="stylesheet">
<style>
  :root {
    --backdrop: #222222;
    --card: #050505;
    --ink: #ffffff;
    --ink-dark: #0a0a0a;
    --shade: #8e9092;
  }
  * { margin: 0; padding: 0; box-sizing: border-box; }
  html, body {
    width: 1200px; height: 711px; overflow: hidden;
    background: var(--backdrop);
    font-family: "Open Sans", sans-serif;
  }
  .stage { position: relative; width: 1200px; height: 711px; }
  .card {
    position: absolute; top: 100px;
    width: 290px; height: 510px;
    background: var(--card);
    border-radius: 26px;
    overflow: hidden;
    color: var(--ink);
  }
  .card--front { left: 295px; }
  .card--back { left: 615px; }

  /* front */
  .front-brand {
    position: absolute; inset: 0;
    display: flex; flex-direction: column; align-items: center; justify-content: center;
    gap: 22px;
  }
  .front-brand__square { width: 46px; height: 46px; background: var(--ink); }
  .front-brand__name {
    font-weight: 700; font-size: 30px; line-height: 1.15;
    text-align: center; text-transform: uppercase; letter-spacing: 1px;
  }

  /* back */
  .back-head { position: absolute; top: 0; left: 0; width: 290px; height: 240px; }
  .back-brand {
    position: absolute; top: 70px; left: 0; width: 290px;
    display: flex; align-items: center; justify-content: center; gap: 10px;
    color: var(--ink-dark);
  }
  .back-brand__square { width: 22px; height: 22px; background: var(--ink-dark); }
  .back-brand__name {
    font-weight: 700; font-size: 17px; line-height: 1.1; text-transform: uppercase;
  }
  .person { position: absolute; top: 258px; width: 100%; text-align: center; }
  .person__name { font-weight: 700; font-size: 22px; letter-spacing: 1px; }
  .person__role { font-size: 12px; margin-top: -2px; }
  .icon-row {
    position: absolute; top: 316px; left: 0; width: 100%;
    display: flex; align-items: center; justify-content: center; gap: 6px;
  }
  .icon-row__rule { width: 42px; height: 1px; background: var(--ink); margin: 0 8px; }
  .icon { width: 22px; height: 22px; background: var(--ink); border-radius: 6px; display: flex; align-items: center; justify-content: center; }
  .contact { position: absolute; top: 352px; width: 100%; text-align: center; font-size: 13px; line-height: 19px; }
  .divider { position: absolute; top: 438px; left: 40px; width: 210px; height: 1px; background: var(--ink); }
  .address { position: absolute; top: 448px; width: 100%; text-align: center; font-size: 12.5px; line-height: 18px; }
</style>
</head>
<body>
<main class="stage">
  <section class="card card--front">
    <div class="front-brand">
      <span class="front-brand__square"></span>
      <p class="front-brand__name">Cedar Ridge<br>Mechanical</p>
    </div>
  </section>

  <section class="card card--back">
    <svg class="back-head" viewBox="0 0 290 240" aria-hidden="true">
      <path d="M0 0 H290 V150 C290 215 220 238 145 238 C70 238 0 215 0 150 Z" fill="var(--shade)"/>
      <path d="M0 0 H284 V140 C284 200 218 226 142 226 C66 226 0 200 0 140 Z" fill="var(--ink)"/>
    </svg>
    <div class="back-brand">
      <span class="back-brand__square"></span>
      <p class="back-brand__name">Cedar Ridge<br>Mechanical</p>
    </div>

    <div class="person">
      <p class="person__name">DANIEL REYES</p>
      <p class="person__role">Managing Director</p>
    </div>

    <div class="icon-row">
      <span class="icon-row__rule"></span>
      <span class="icon"><svg width="14" height="14" viewBox="0 0 14 14"><path d="M3 1 L5 1 L6 4 L4.5 5.5 C5.3 7.2 6.8 8.7 8.5 9.5 L10 8 L13 9 L13 11 C13 12 12 13 11 13 C5.5 13 1 8.5 1 3 C1 2 2 1 3 1 Z" fill="var(--ink-dark)"/></svg></span>
      <span class="icon"><svg width="14" height="14" viewBox="0 0 14 14"><rect x="3.5" y="1" width="7" height="12" rx="1.3" fill="none" stroke="var(--ink-dark)" stroke-width="1.5"/><circle cx="7" cy="11" r="0.8" fill="var(--ink-dark)"/></svg></span>
      <span class="icon"><svg width="14" height="14" viewBox="0 0 14 14"><rect x="1" y="3" width="12" height="8.5" fill="none" stroke="var(--ink-dark)" stroke-width="1.4"/><path d="M1 3 L7 8 L13 3" fill="none" stroke="var(--ink-dark)" stroke-width="1.4"/></svg></span>
      <span class="icon"><svg width="14" height="14" viewBox="0 0 14 14"><circle cx="7" cy="7" r="5.5" fill="none" stroke="var(--ink-dark)" stroke-width="1.3"/><ellipse cx="7" cy="7" rx="2.3" ry="5.5" fill="none" stroke="var(--ink-dark)" stroke-width="1.1"/><path d="M1.5 7 H12.5" stroke="var(--ink-dark)" stroke-width="1.1"/></svg></span>
      <span class="icon-row__rule"></span>
    </div>

    <div class="contact">
      <p>555-201-4417</p>
      <p>555-201-8832</p>
      <p>info@cedarridgemech.com</p>
      <p>www.cedarridgemech.com</p>
    </div>
    <span class="divider"></span>
    <div class="address">
      <p>4820 Harbor View Rd Suite</p>
      <p>210 Tacoma, Washington 98402</p>
    </div>
  </section>
</main>
</body>
</html>
```